Letterhead and business card design

We have recently had a logo designed by brandnestly. now we need a corporate identity with business card and lettehead design.

Target Market(s)

law firms corporates

Industry/Entity Type

Business

Requirements
Should not have
• cheesy detecive stuff like magnifying glasses etxcc

```html
<!DOCTYPE html>
<html lang="en">
<head>
<meta charset="utf-8">
<title>Hallworth Pryce – Business Card</title>
<link rel="stylesheet" href="https://fonts.googleapis.com/css2?family=Jost:wght@400;600&display=swap">
<style>
  :root {
    --backdrop: #e8e7ed;
    --card-white: #f7f8f9;
    --ink: #4a4d4f;
    --ink-soft: #6a6e70;
    --steel: #8c9393;
    --steel-dark: #6f7676;
    --steel-light: #a3a9a9;
    --back-ink: #dfe3e3;
  }
  * { margin: 0; padding: 0; box-sizing: border-box; }
  html, body {
    width: 1200px; height: 934px; overflow: hidden;
    background: var(--backdrop);
  }
  .sheet {
    position: relative; width: 1200px; height: 934px;
    display: flex; flex-direction: column; align-items: center;
    justify-content: center; gap: 40px;
  }
  .card {
    position: relative; width: 620px; height: 354px;
    box-shadow: 0 6px 18px rgba(60, 60, 80, 0.18);
    overflow: hidden;
    font-family: "Jost", sans-serif;
  }
  .brand-name {
    position: absolute; left: 0; right: 0; text-align: center;
    font-family: "Jost", sans-serif; font-weight: 400;
    font-size: 36px; letter-spacing: 0.06em; white-space: nowrap;
  }

  /* Back of card */
  .card-back {
    background: linear-gradient(100deg, var(--steel-light) 0%, var(--steel) 55%, var(--steel-dark) 100%);
    color: var(--back-ink);
  }
  .card-back .brand-name { top: 92px; color: var(--back-ink); }
  .card-back .website {
    position: absolute; bottom: 44px; left: 0; right: 0; text-align: center;
    font-size: 15px; letter-spacing: 0.03em;
  }

  /* Front of card */
  .card-front { background: var(--card-white); color: var(--ink); }
  .card-front .brand-name { top: 72px; color: var(--ink); }
  .holder {
    position: absolute; top: 176px; left: 0; right: 0; text-align: center;
  }
  .holder-name { font-weight: 600; font-size: 17px; letter-spacing: 0.04em; }
  .holder-role { font-size: 13px; color: var(--ink-soft); }
  .contact {
    position: absolute; bottom: 44px; left: 0; right: 0; text-align: center;
    font-size: 13px; line-height: 1.55; color: var(--ink-soft);
  }
  .contact b { font-weight: 600; color: var(--ink); }
  .contact .sep { margin: 0 6px; }
  .card-band {
    position: absolute; bottom: 0; left: 0; right: 0; height: 26px;
    background: linear-gradient(90deg, var(--steel-light), var(--steel-dark));
  }
</style>
</head>
<body>
<main class="sheet">
  <section class="card card-back" aria-label="Business card back">
    <div class="brand-name">Hallworth Pryce</div>
    <div class="website">www.hallworthpryce.co.nz</div>
  </section>

  <section class="card card-front" aria-label="Business card front">
    <div class="brand-name">Hallworth Pryce</div>
    <div class="holder">
      <div class="holder-name">MARCUS PRYCE</div>
      <div class="holder-role">Director</div>
    </div>
    <div class="contact">
      <div>PO Box 318, Keswick Street, Wellford, New Zealand</div>
      <div><b>Tel:</b> +64 9 555 0142<span class="sep">•</span><b>Fax:</b> +64 9 555 0187<span class="sep">•</span><b>Email:</b> marcus@hallworthpryce.co.nz</div>
    </div>
    <div class="card-band"></div>
  </section>
</main>
</body>
</html>
```